RTavenor Business Cards & Letterhead

I have a logo but need a design for some new business cards. We are a Design-Build Firm that specializes in the design and construction of commercial projects.
the cards need to be professional. no cartoon stuff.
i would like to have the cards in AI format so I can update the card as needed. Logo is provided.
Our Address is: 4187 Marlowe Ct. Apex, North Carolina 27614

```html
<!DOCTYPE html>
<html lang="en">
<head>
<meta charset="utf-8">
<title>RTavenor Letterhead</title>
<link href="https://fonts.googleapis.com/css2?family=Lato:wght@400;700&family=Open+Sans:wght@400&family=Tangerine:wght@700&display=swap" rel="stylesheet">
<style>
  :root {
    --backdrop: #e3e3e3;
    --paper: #ffffff;
    --brand-blue: #0a6aa6;
    --brand-grey: #707070;
    --ink: #1c1c1c;
  }
  * { margin: 0; padding: 0; box-sizing: border-box; }
  html, body {
    width: 1200px; height: 1141px; overflow: hidden;
    background: var(--backdrop);
  }
  .letterhead {
    position: absolute; left: 211px; top: 20px;
    width: 778px; height: 1101px;
    background: var(--paper);
    box-shadow: 0 2px 8px rgba(0,0,0,0.18);
    overflow: hidden;
    font-family: 'Lato', sans-serif; color: var(--ink);
  }
  .brand {
    position: absolute; left: 39px; top: 76px;
    display: flex; align-items: center; gap: 10px;
  }
  .brand-square { width: 34px; height: 34px; background: var(--brand-blue); }
  .brand-name {
    font-family: 'Lato', sans-serif; font-weight: 700;
    font-size: 54px; line-height: 1; color: var(--brand-grey);
    letter-spacing: 0.5px;
  }
  .contact {
    position: absolute; left: 557px; top: 54px;
    border-left: 2px solid var(--brand-blue);
    padding-left: 14px; height: 89px;
    font-family: 'Open Sans', sans-serif; font-size: 14px; line-height: 17.5px;
    color: var(--ink);
  }
  .contact-address { margin-top: -3px; margin-bottom: 8px; }
  .contact-line { display: flex; align-items: center; gap: 4px; }
  .contact-line svg { width: 10px; height: 10px; fill: var(--brand-blue); flex: none; }
  .letter { position: absolute; left: 39px; width: 701px; font-size: 16px; line-height: 18.4px; }
  .date { top: 253px; }
  .recipient { top: 291px; }
  .company { top: 345px; }
  .salutation { top: 421px; font-weight: 700; font-size: 20px; }
  .body { top: 466px; }
  .body p { text-align: justify; font-size: 15.6px; line-height: 17.3px; margin-bottom: 17px; letter-spacing: -0.05px; }
  .closing { top: 780px; }
  .signature {
    position: absolute; left: 39px; top: 884px;
    font-family: 'Tangerine', cursive; font-weight: 700; font-size: 42px; color: var(--ink);
  }
  .footer-rule {
    position: absolute; left: 0; bottom: 104px; width: 778px; height: 6px;
    background: var(--brand-grey);
  }
  .footer-band {
    position: absolute; left: 0; bottom: 0; width: 778px; height: 96px;
    background: var(--brand-blue);
  }
</style>
</head>
<body>
  <div class="letterhead">
    <div class="brand">
      <span class="brand-square"></span>
      <span class="brand-name">RTavenor</span>
    </div>

    <div class="contact">
      <div class="contact-address">4187 Marlowe Ct. Apex,<br>North Carolina 27614</div>
      <div class="contact-line">
        <svg viewBox="0 0 10 10"><path d="M2 0.5 L3.8 2.6 L2.8 3.7 C3.4 5 4.9 6.5 6.3 7.1 L7.4 6.1 L9.5 8 L8.2 9.5 C4.5 9.2 0.8 5.5 0.5 1.8 Z"/></svg>
        <span>123 456 789</span>
      </div>
      <div class="contact-line">
        <svg viewBox="0 0 10 10"><path d="M0.5 2 H9.5 V8 H0.5 Z M1.2 2.6 L5 5.4 L8.8 2.6" stroke="#fff" stroke-width="0.8"/></svg>
        <span>info@yourgmail.com</span>
      </div>
      <div class="contact-line">
        <svg viewBox="0 0 10 10"><circle cx="5" cy="5" r="4.5"/><path d="M2 3.5 C3.5 4 4 5 3.2 6.5 M6 1.5 C6.5 3 7.8 3.6 8.8 3.8 M5.5 6.5 C6.5 7 7 8 6.8 9" stroke="#fff" stroke-width="0.8" fill="none"/></svg>
        <span>www.yourwebsite.com</span>
      </div>
    </div>

    <div class="letter date">January-03-2020</div>
    <div class="letter recipient">Mr, John Doe<br>President</div>
    <div class="letter company">Ridge Corporation<br>123 Street Name, Suite# 10<br>City, State, 120023</div>
    <div class="letter salutation">Dear Mr, John</div>

    <div class="letter body">
      <p>Lorem ipsum dolor sit amet, consectetur adipiscing elit, sed do eiusmod tempor incididunt ut labore et dolore magna aliqua. Ut enim ad minim veniam, quis nostrud exercitation ullamco laboris nisi ut aliquip ex ea commodo consequat. Duis aute irure dolor in reprehenderit in voluptate velit esse cillum dolore eu fugiat nulla pariatur.</p>
      <p>Lorem ipsum dolor sit amet, consectetur adipiscing elit, sed do eiusmod tempor incididunt ut labore et dolore magna aliqua. Ut enim ad minim veniam, quis nostrud exercitation ullamco laboris nisi ut aliquip ex ea commodo consequat. Duis aute irure dolor in reprehenderit in voluptate velit esse cillum dolore eu fugiat nulla pariatur.</p>
      <p>Lorem ipsum dolor sit amet, consectetur adipiscing elit, sed do eiusmod tempor incididunt ut labore et dolore magna aliqua. Ut enim ad minim veniam, quis nostrud exercitation ullamco laboris nisi ut aliquip ex ea commodo consequat.</p>
      <p>Excepteur sint occaecat cupidatat non proident, sunt in culpa qui officia deserunt mollit anim id est laborum. re et dolore magnam aliquam quaerat voluptatem.</p>
    </div>

    <div class="letter closing">Regards</div>
    <div class="signature">Elena Marsh</div>

    <div class="footer-rule" aria-hidden="true"></div>
    <div class="footer-band" aria-hidden="true"></div>
  </div>
</body>
</html>
```